Website design for legal tech start up in Switzerland (B2B)

We are for a legal tech start up in Switzerland called KOVA. We have been running since August 2016. This will be our first live website.

We need a website designed and business card design for our start-up in Switzerland. We also need the Web design to be converted into HTML and CSS files.

Function of website:
• To inform potential customers of our services
• Form a key part of our digital marketing and sales footprint.
• Branding

Please find attached logo.
Updates

Project Deadline Extended Reason: Giving us time to review submissions and provide opportunity for more submissions. Added Thursday, February 16, 2017

Project Deadline Extended
Reason: Looking for more idea's not necessarily set on blue and grey colours only.

Target Market(s)

B2B tech powered legal services.

Industry/Entity Type

Legal

Contact Information for Business Card

Lean and slick design.

Coding

Coded - Design and coding required

Number of Pages Required

5+ page

Requirements
Must have
• VERY LEAN AND CLEAN DESIGN!
• We have received many great standard designs, but we are looking for something more out-of-the box: You can get inspiration from these designs: http://www.pixelvane.com/websites/clean/
• Thanks!!
• Easy content management system
• Well structured coding for additional development
• Responsive webpage for all types of devices
• SEO optimized
• Tabs (Home, services, team, careers, blog, contact us)
• Colour scheme complementary to logo
Nice to have
• Look and Design - Approachable, High-tech, Modern
• Easy to add chat bot capability in future
Should not have
• Too busy/ too much clutter
• Not take to long to load

```html
<!DOCTYPE html>
<html lang="en">
<head>
<meta charset="utf-8">
<title>KOVA – Legal Advisor</title>
<link href="https://fonts.googleapis.com/css2?family=Lato:wght@300;400;700;900&display=swap" rel="stylesheet">
<style>
:root{
  --navy:#1d3e72;
  --navy-deep:#142d55;
  --ink:#2b2b2b;
  --text:#555;
  --muted:#888;
  --paper:#ffffff;
  --mist:#eeeff1;
  --line:#d6d8dc;
  --dark:#1c1f26;
}
*{box-sizing:border-box;margin:0;padding:0}
html,body{width:1200px;height:5172px;overflow:hidden}
body{font-family:'Lato',Arial,sans-serif;color:var(--text);background:var(--paper);font-size:15px;line-height:1.5}
section,header,footer{position:relative;width:1200px;overflow:hidden}
.title{font-size:38px;font-weight:400;color:var(--ink);text-align:center;letter-spacing:1px;text-transform:uppercase}
.title b{font-weight:900;color:var(--navy)}
.divider{display:block;margin:10px auto 0;width:200px;height:14px}
.small{font-size:13px;line-height:1.55;color:var(--text)}

/* header */
.site-header{height:76px;display:flex;align-items:center;justify-content:space-between;padding:0 40px 0 80px;background:var(--paper)}
.brand{font-size:44px;font-weight:900;color:var(--ink);letter-spacing:2px}
.head-right{display:flex;align-items:center;gap:26px}
.phone{display:flex;align-items:center;gap:10px;font-size:26px;font-weight:700;color:var(--ink)}
.phone .dot{width:30px;height:30px;border-radius:50%;background:var(--ink);display:flex;align-items:center;justify-content:center}
.menu-btn{width:46px;height:40px;background:var(--ink);display:flex;flex-direction:column;justify-content:center;gap:6px;padding:0 11px}
.menu-btn span{display:block;height:3px;background:#fff}

/* hero */
.hero{height:527px}
.hero-photo{position:absolute;inset:0;background:linear-gradient(100deg,#0d1526 0%,#1b2740 38%,#3a5d8c 60%,#8fa9c9 78%,#d9b9b6 100%)}
.hero-shade{position:absolute;inset:0;background:linear-gradient(90deg,rgba(10,18,34,.85) 0%,rgba(10,18,34,.4) 45%,rgba(10,18,34,0) 65%)}
.hero-copy{position:absolute;left:84px;top:200px;color:#fff}
.hero-copy h1{font-size:46px;font-weight:400;line-height:1.2;letter-spacing:1px}
.btn-line{display:inline-block;margin-top:32px;border:2px solid #fff;color:#fff;font-size:19px;padding:12px 22px;letter-spacing:.5px}

/* about */
.about{height:473px;background:linear-gradient(180deg,#f4f5f7,#e9ebee)}
.about .title{padding-top:44px}
.about p.lead{width:1080px;margin:34px auto 0;text-align:center;font-size:14px;line-height:1.6;color:var(--text)}
.mv-row{display:flex;justify-content:center;gap:66px;margin-top:42px}
.mv-card{width:340px;height:110px;background:#fff;box-shadow:4px 6px 10px rgba(0,0,0,.18);display:flex;gap:18px;padding:20px 22px}
.icon-sq{flex:none;width:60px;height:60px;background:var(--navy);display:flex;align-items:center;justify-content:center}
.mv-card h3{font-size:20px;font-weight:700;color:var(--ink);margin-bottom:4px}

/* services */
.services{height:855px;background:var(--paper)}
.services .title{padding-top:40px}
.services .intro{width:1060px;margin:34px auto 0;text-align:center;font-size:16px;color:var(--text)}
.services .intro a{color:var(--navy);text-decoration:underline}
.svc-grid{display:grid;grid-template-columns:repeat(3,293px);gap:58px 60px;justify-content:center;margin-top:38px}
.svc-card{height:260px;background:var(--mist);position:relative;text-align:center;padding-top:28px}
.svc-card.is-active{background:var(--navy)}
.svc-card .icon-sq{margin:0 auto}
.svc-card.is-active .icon-sq{background:#fff}
.svc-card h3{font-size:20px;font-weight:400;color:var(--ink);margin-top:26px}
.svc-card.is-active h3{color:#fff}
.svc-card p{font-size:13px;color:var(--text);margin-top:6px}
.svc-card.is-active p{color:#d8e0ee}
.plus{position:absolute;left:50%;bottom:-18px;transform:translateX(-50%);width:36px;height:36px;border-radius:50%;background:var(--ink);color:#fff;font-size:24px;line-height:34px;text-align:center;font-weight:700}

/* advice band */
.advice{height:372px}
.advice-photo{position:absolute;inset:0;background:linear-gradient(90deg,#3a3a3a,#8b8b8b 35%,#d5d5d5 50%,#7c7c7c 70%,#2f2f2f)}
.advice-box{position:absolute;left:380px;top:72px;width:440px;height:240px;background:rgba(29,62,114,.92);color:#fff;padding:20px 34px}
.advice-box h2{font-size:28px;font-weight:700;letter-spacing:.5px;text-transform:uppercase;white-space:nowrap}
.advice-row{display:flex;align-items:center;gap:16px;margin-top:12px}
.circ{width:40px;height:40px;border-radius:50%;border:2px solid #fff;display:flex;align-items:center;justify-content:center;flex:none}
.advice-row .big{font-size:22px;white-space:nowrap}
.advice .or{font-size:22px;font-weight:700;text-align:center;margin-top:2px}
.call-small{font-size:12px;color:#cdd6e6}
.call-num{font-size:28px;line-height:1.1;white-space:nowrap}

/* why */
.why{height:604px;background:linear-gradient(180deg,#fff,#eceef1)}
.why .title{padding-top:48px}
.why-ribbon{position:absolute;left:60px;right:40px;top:268px;height:130px;border-radius:65px;background:linear-gradient(90deg,#3c3f46,#1d3e72 50%,#3c3f46)}
.why-label{position:absolute;width:240px;text-align:center}
.why-label h4{font-size:19px;font-weight:700;color:var(--ink)}
.why-label p{font-size:13px;color:var(--text)}
.why-label .go{display:inline-block;margin-top:8px;width:26px;height:26px;border-radius:50%;background:var(--ink);color:#fff;font-size:14px;line-height:26px}

/* team */
.team-band{height:351px}
.city-photo{position:absolute;inset:0;background:linear-gradient(180deg,#6e86a8 0%,#3c5a82 45%,#1d2d47 100%)}
.band-box{position:absolute;left:380px;width:440px;background:rgba(29,62,114,.85);color:#fff;text-align:center;padding:22px 30px}
.band-box h2{font-size:30px;font-weight:400;text-transform:uppercase;letter-spacing:1px}
.band-box p{font-size:13px;color:#dbe3f0;margin-top:10px}
.team{height:328px;background:var(--paper)}
.team-row{display:flex;justify-content:center;gap:38px;padding-top:32px}
.member{width:170px;text-align:center}
.member .photo{height:170px;border:5px solid #fff;box-shadow:0 0 0 1px var(--line),2px 4px 10px rgba(0,0,0,.2);background:linear-gradient(180deg,#c9ccd2,#6d7480)}
.member h4{font-size:18px;font-weight:400;color:var(--ink);margin-top:12px}
.member .acts{display:flex;justify-content:center;gap:12px;margin-top:10px}
.member .acts span{width:24px;height:24px;border-radius:50%;background:var(--mist);display:flex;align-items:center;justify-content:center}

/* blog */
.blog-band{height:362px}
.blog-band .city-photo{background:linear-gradient(180deg,#5f6f86 0%,#2f3f58 50%,#121b2b 100%)}
.blog{height:459px;background:var(--paper)}
.blog-row{display:flex;justify-content:center;gap:40px;padding-top:38px}
.post{width:330px;height:340px;background:#fff;box-shadow:0 1px 6px rgba(0,0,0,.18)}
.post .pic{height:176px}
.post .body{display:flex;gap:14px;padding:16px 14px}
.date{flex:none;width:38px;height:38px;background:var(--navy);color:#fff;text-align:center;font-size:14px;font-weight:700;line-height:38px}
.post h4{font-size:15px;font-weight:700;color:var(--ink)}
.post .meta{font-size:12px;color:var(--muted);margin:4px 0 10px}
.post p{font-size:12.5px;color:var(--text)}
.dots{display:flex;justify-content:center;gap:10px;margin-top:30px}
.dots span{width:11px;height:11px;border-radius:50%;background:#c9ccd2}
.dots span.on{background:var(--ink)}

/* callback */
.callback{height:283px;background:var(--navy);color:#fff}
.callback h2{position:absolute;left:88px;top:44px;font-size:37px;font-weight:400;line-height:1.15}
.callback .cb-text{position:absolute;left:88px;top:150px;width:320px;font-size:13px;color:#d8e0ee}
.cb-form{position:absolute;left:456px;top:36px;width:650px}
.cb-form .lbl{font-size:15px}
.fields{display:grid;grid-template-columns:1fr 1fr;gap:14px 64px;margin-top:12px}
.field{height:40px;background:#fff;color:#666;font-size:14px;padding:9px 12px}
.submit{display:inline-block;margin-top:14px;background:var(--dark);color:#fff;font-size:16px;letter-spacing:2px;padding:10px 22px}

/* footer */
.site-footer{height:430px;color:#fff}
.foot-photo{position:absolute;inset:0;background:linear-gradient(180deg,#1b2233 0%,#202a3f 55%,#2b3650 100%)}
.foot-cols{position:absolute;top:46px;left:160px;right:100px;display:flex;justify-content:space-between;text-align:center;font-size:13px}
.foot-cols div{width:300px}
.foot-cols svg{display:block;margin:0 auto 16px}
.foot-rule{position:absolute;left:160px;right:110px;top:130px;height:1px;background:rgba(255,255,255,.3)}
.foot-brand{position:absolute;top:160px;width:100%;text-align:center;font-size:56px;font-weight:900;letter-spacing:3px}
.foot-text{position:absolute;top:244px;left:360px;width:480px;text-align:center;font-size:13px;color:#c8cfdb}
.hours{position:absolute;top:306px;width:100%;display:flex;justify-content:center;gap:46px;font-size:13px;font-weight:700}
.foot-btn{position:absolute;top:356px;left:538px;border:1px solid #fff;font-size:14px;padding:5px 16px;letter-spacing:1px}
.copy{height:52px;background:var(--navy-deep);color:#fff;display:flex;align-items:center;justify-content:space-between;padding:0 34px;font-size:13px}
.social{display:flex;gap:10px}
.social span{width:30px;height:30px;border-radius:50%;display:block}
</style>
</head>
<body>

<header class="site-header">
  <div class="brand">KOVA</div>
  <div class="head-right">
    <div class="phone">
      <span class="dot"><svg width="16" height="16" viewBox="0 0 24 24"><path fill="#fff" d="M6.6 10.8a15 15 0 0 0 6.6 6.6l2.2-2.2c.3-.3.7-.4 1-.2 1.1.4 2.3.6 3.6.6.6 0 1 .4 1 1V20c0 .6-.4 1-1 1A17 17 0 0 1 3 4c0-.6.4-1 1-1h3.5c.6 0 1 .4 1 1 0 1.3.2 2.5.6 3.6.1.3 0 .7-.2 1z"/></svg></span>
      +41 22 555 0142
    </div>
    <div class="menu-btn"><span></span><span></span><span></span></div>
  </div>
</header>

<section class="hero">
  <div class="hero-photo" role="img" aria-label="City skyline of glass office towers at dusk"></div>
  <div class="hero-shade"></div>
  <div class="hero-copy">
    <h1>WE ARE EXPERT IN<br>LEGAL ADVISOR</h1>
    <span class="btn-line">GET A FREE CONSULTATION</span>
  </div>
</section>

<section class="about">
  <h2 class="title">About <b>KOVA</b></h2>
  <svg class="divider" viewBox="0 0 200 14"><line x1="0" y1="7" x2="200" y2="7" stroke="#2b2b2b" stroke-width="2"/></svg>
  <p class="lead">We help companies handle contracts, compliance and disputes with clear advice and smart tools. Our team pairs experienced lawyers with software that saves time, so clients get fast answers, fair prices and full insight into every step of their matter. From first question to final signature, we keep the process simple, open and secure. We work with start ups, growing firms and large groups across many sectors, and we tailor each service to the way our clients already work. Every file is handled by a named lawyer who knows your business and stays your contact from start to end.</p>
  <div class="mv-row">
    <div class="mv-card">
      <div class="icon-sq"><svg width="32" height="32" viewBox="0 0 32 32" fill="#fff"><circle cx="16" cy="10" r="5"/><path d="M7 27c0-6 4-9 9-9s9 3 9 9z"/><circle cx="6" cy="13" r="3"/><circle cx="26" cy="13" r="3"/></svg></div>
      <div><h3>Our Mission</h3><p class="small">Make legal help quick, clear and fair for every business we serve.</p></div>
    </div>
    <div class="mv-card">
      <div class="icon-sq"><svg width="32" height="32" viewBox="0 0 32 32" fill="none" stroke="#fff" stroke-width="2.5"><circle cx="16" cy="16" r="12"/><circle cx="16" cy="16" r="6"/><circle cx="16" cy="16" r="1.5" fill="#fff"/></svg></div>
      <div><h3>Our Vision</h3><p class="small">A world where sound legal advice is open to every company.</p></div>
    </div>
  </div>
</section>

<section class="services">
  <h2 class="title">Our Services</h2>
  <svg class="divider" viewBox="0 0 200 14"><line x1="0" y1="7" x2="88" y2="7" stroke="#bbb"/><path d="M95 2l10 10M105 2L95 12" stroke="#999" stroke-width="2"/><line x1="112" y1="7" x2="200" y2="7" stroke="#bbb"/></svg>
  <p class="intro">We were also the first to realize that the real estate world was changing, and we needed to change with it to continue innovating. Now we are investors, founders and developers behind some of the most intriguing companies in the business. <a>Contact us</a> to learn more.</p>
  <div class="svc-grid">
    <div class="svc-card is-active">
      <div class="icon-sq"><svg width="30" height="30" viewBox="0 0 30 30" fill="#1d3e72"><circle cx="15" cy="15" r="6"/><rect x="13" y="2" width="4" height="6"/><rect x="13" y="22" width="4" height="6"/><rect x="2" y="13" width="6" height="4"/><rect x="22" y="13" width="6" height="4"/></svg></div>
      <h3>Information Management</h3><p>Clear records kept safe<br>and easy to find</p><span class="plus">–</span>
    </div>
    <div class="svc-card">
      <div class="icon-sq"><svg width="30" height="30" viewBox="0 0 30 30" fill="#fff"><circle cx="15" cy="9" r="6"/><path d="M4 28c0-7 5-10 11-10s11 3 11 10z"/></svg></div>
      <h3>Case Support</h3><p>Hands on help for each<br>stage of your case</p><span class="plus">+</span>
    </div>
    <div class="svc-card">
      <div class="icon-sq"><svg width="30" height="30" viewBox="0 0 30 30" fill="#fff"><rect x="3" y="5" width="24" height="16" rx="1"/><rect x="11" y="22" width="8" height="3"/><rect x="7" y="25" width="16" height="2"/></svg></div>
      <h3>Application Development</h3><p>Custom tools built for<br>your legal workflow</p><span class="plus">+</span>
    </div>
    <div class="svc-card">
      <div class="icon-sq"><svg width="30" height="30" viewBox="0 0 30 30" fill="#fff"><path d="M15 3c6 4 8 10 0 22C7 13 9 7 15 3z"/><rect x="14" y="18" width="2" height="10"/></svg></div>
      <h3>Environmental Litigation</h3><p>Guidance on rules that<br>protect land and air</p><span class="plus">+</span>
    </div>
    <div class="svc-card">
      <div class="icon-sq"><svg width="30" height="30" viewBox="0 0 30 30" fill="none" stroke="#fff" stroke-width="3"><circle cx="15" cy="15" r="7"/><path d="M15 2v5M15 23v5M2 15h5M23 15h5M6 6l3 3M21 21l3 3M6 24l3-3M21 9l3-3"/></svg></div>
      <h3>Legal Word Processing</h3><p>Fast drafting of clean<br>and precise documents</p><span class="plus">+</span>
    </div>
    <div class="svc-card">
      <div class="icon-sq"><svg width="30" height="30" viewBox="0 0 30 30" fill="#fff"><rect x="11" y="3" width="8" height="7"/><rect x="3" y="20" width="8" height="7"/><rect x="19" y="20" width="8" height="7"/><path d="M15 10v5M7 20v-5h16v5" stroke="#fff" stroke-width="2" fill="none"/></svg></div>
      <h3>Procurement Support</h3><p>Sound advice on tenders<br>and supplier deals</p><span class="plus">+</span>
    </div>
  </div>
</section>

<section class="advice">
  <div class="advice-photo" role="img" aria-label="Business people shaking hands in an office"></div>
  <div class="advice-box">
    <h2>Need a legal advice ?</h2>
    <div class="advice-row"><span class="circ"><svg width="18" height="18" viewBox="0 0 24 24" fill="#fff"><circle cx="12" cy="8" r="4"/><path d="M4 21c0-5 4-7 8-7s8 2 8 7z"/></svg></span><span class="big">Get A FREE CONSULTATION</span></div>
    <div class="or">OR</div>
    <div class="advice-row"><span class="circ"><svg width="16" height="16" viewBox="0 0 24 24"><path fill="#fff" d="M6.6 10.8a15 15 0 0 0 6.6 6.6l2.2-2.2c.3-.3.7-.4 1-.2 1.1.4 2.3.6 3.6.6.6 0 1 .4 1 1V20c0 .6-.4 1-1 1A17 17 0 0 1 3 4c0-.6.4-1 1-1h3.5c.6 0 1 .4 1 1 0 1.3.2 2.5.6 3.6.1.3 0 .7-.2 1z"/></svg></span><div><div class="call-small">Call Us Today</div><div class="call-num">+41 22 555 0142</div></div></div>
  </div>
</section>

<section class="why">
  <h2 class="title">Why <b>Choose Us ?</b></h2>
  <svg class="divider" viewBox="0 0 200 14"><line x1="0" y1="7" x2="88" y2="7" stroke="#bbb"/><path d="M95 2l10 10M105 2L95 12" stroke="#999" stroke-width="2"/><line x1="112" y1="7" x2="200" y2="7" stroke="#bbb"/></svg>
  <div class="why-ribbon" role="img" aria-label="Decorative navy and charcoal ribbon linking six service icons"></div>
  <div class="why-label" style="left:50px;top:160px"><h4>Strategic Planning</h4><p>Clear goals and steps set<br>out before any action.</p><span class="go">›</span></div>
  <div class="why-label" style="left:410px;top:160px"><h4>Creative</h4><p>Fresh ideas that solve<br>hard legal questions.</p><span class="go">›</span></div>
  <div class="why-label" style="left:770px;top:160px"><h4>Consulting Practice</h4><p>Direct access to senior<br>advisors on each file.</p><span class="go">›</span></div>
  <div class="why-label" style="left:230px;top:432px"><h4>Market Research</h4><p>Facts on your sector that<br>shape sound choices.</p><span class="go">›</span></div>
  <div class="why-label" style="left:590px;top:432px"><h4>High Value</h4><p>Fixed fees and results<br>you can measure.</p><span class="go">›</span></div>
  <div class="why-label" style="left:950px;top:432px"><h4>Translate</h4><p>Work in every major<br>language you need.</p><span class="go">›</span></div>
</section>

<section class="team-band">
  <div class="city-photo" role="img" aria-label="Silhouettes of a business team in front of a city window"></div>
  <div class="band-box" style="top:100px"><h2>Our Team</h2><p>Skilled lawyers and engineers who share one goal: giving clients fast, clear and fair legal help every single day.</p></div>
</section>

<section class="team">
  <div class="team-row">
    <div class="member"><div class="photo" role="img" aria-label="Portrait of a team member"></div><h4>Lorem Ipsum</h4><div class="acts"><span><svg width="11" height="11" viewBox="0 0 24 24" fill="#1d3e72"><path d="M6.6 10.8a15 15 0 0 0 6.6 6.6l2.2-2.2c.3-.3.7-.4 1-.2 1.1.4 2.3.6 3.6.6.6 0 1 .4 1 1V20c0 .6-.4 1-1 1A17 17 0 0 1 3 4c0-.6.4-1 1-1h3.5c.6 0 1 .4 1 1 0 1.3.2 2.5.6 3.6.1.3 0 .7-.2 1z"/></svg></span><span><svg width="11" height="11" viewBox="0 0 24 24" fill="#1d3e72"><rect x="2" y="5" width="20" height="14"/></svg></span><span><svg width="11" height="11" viewBox="0 0 24 24" fill="#1d3e72"><circle cx="6" cy="12" r="3"/><circle cx="18" cy="5" r="3"/><circle cx="18" cy="19" r="3"/></svg></span></div></div>
    <div class="member"><div class="photo" role="img" aria-label="Portrait of a team member"></div><h4>Lorem Ipsum</h4><div class="acts"><span><svg width="11" height="11" viewBox="0 0 24 24" fill="#1d3e72"><path d="M6.6 10.8a15 15 0 0 0 6.6 6.6l2.2-2.2c.3-.3.7-.4 1-.2 1.1.4 2.3.6 3.6.6.6 0 1 .4 1 1V20c0 .6-.4 1-1 1A17 17 0 0 1 3 4c0-.6.4-1 1-1h3.5c.6 0 1 .4 1 1 0 1.3.2 2.5.6 3.6.1.3 0 .7-.2 1z"/></svg></span><span><svg width="11" height="11" viewBox="0 0 24 24" fill="#1d3e72"><rect x="2" y="5" width="20" height="14"/></svg></span><span><svg width="11" height="11" viewBox="0 0 24 24" fill="#1d3e72"><circle cx="6" cy="12" r="3"/><circle cx="18" cy="5" r="3"/><circle cx="18" cy="19" r="3"/></svg></span></div></div>
    <div class="member"><div class="photo" role="img" aria-label="Portrait of a team member"></div><h4>Lorem Ipsum</h4><div class="acts"><span><svg width="11" height="11" viewBox="0 0 24 24" fill="#1d3e72"><path d="M6.6 10.8a15 15 0 0 0 6.6 6.6l2.2-2.2c.3-.3.7-.4 1-.2 1.1.4 2.3.6 3.6.6.6 0 1 .4 1 1V20c0 .6-.4 1-1 1A17 17 0 0 1 3 4c0-.6.4-1 1-1h3.5c.6 0 1 .4 1 1 0 1.3.2 2.5.6 3.6.1.3 0 .7-.2 1z"/></svg></span><span><svg width="11" height="11" viewBox="0 0 24 24" fill="#1d3e72"><rect x="2" y="5" width="20" height="14"/></svg></span><span><svg width="11" height="11" viewBox="0 0 24 24" fill="#1d3e72"><circle cx="6" cy="12" r="3"/><circle cx="18" cy="5" r="3"/><circle cx="18" cy="19" r="3"/></svg></span></div></div>
    <div class="member"><div class="photo" role="img" aria-label="Portrait of a team member"></div><h4>Lorem Ipsum</h4><div class="acts"><span><svg width="11" height="11" viewBox="0 0 24 24" fill="#1d3e72"><path d="M6.6 10.8a15 15 0 0 0 6.6 6.6l2.2-2.2c.3-.3.7-.4 1-.2 1.1.4 2.3.6 3.6.6.6 0 1 .4 1 1V20c0 .6-.4 1-1 1A17 17 0 0 1 3 4c0-.6.4-1 1-1h3.5c.6 0 1 .4 1 1 0 1.3.2 2.5.6 3.6.1.3 0 .7-.2 1z"/></svg></span><span><svg width="11" height="11" viewBox="0 0 24 24" fill="#1d3e72"><rect x="2" y="5" width="20" height="14"/></svg></span><span><svg width="11" height="11" viewBox="0 0 24 24" fill="#1d3e72"><circle cx="6" cy="12" r="3"/><circle cx="18" cy="5" r="3"/><circle cx="18" cy="19" r="3"/></svg></span></div></div>
    <div class="member"><div class="photo" role="img" aria-label="Portrait of a team member"></div><h4>Lorem Ipsum</h4><div class="acts"><span><svg width="11" height="11" viewBox="0 0 24 24" fill="#1d3e72"><path d="M6.6 10.8a15 15 0 0 0 6.6 6.6l2.2-2.2c.3-.3.7-.4 1-.2 1.1.4 2.3.6 3.6.6.6 0 1 .4 1 1V20c0 .6-.4 1-1 1A17 17 0 0 1 3 4c0-.6.4-1 1-1h3.5c.6 0 1 .4 1 1 0 1.3.2 2.5.6 3.6.1.3 0 .7-.2 1z"/></svg></span><span><svg width="11" height="11" viewBox="0 0 24 24" fill="#1d3e72"><rect x="2" y="5" width="20" height="14"/></svg></span><span><svg width="11" height="11" viewBox="0 0 24 24" fill="#1d3e72"><circle cx="6" cy="12" r="3"/><circle cx="18" cy="5" r="3"/><circle cx="18" cy="19" r="3"/></svg></span></div></div>
  </div>
</section>

<section class="blog-band">
  <div class="city-photo" role="img" aria-label="Night view of city skyscrapers"></div>
  <div class="band-box" style="top:96px"><h2>Latest Blog Posts</h2><p>News, guides and views from our lawyers on the rules that shape modern business, written in plain words for busy teams who need answers fast.</p></div>
</section>

<section class="blog">
  <div class="blog-row">
    <article class="post"><div class="pic" role="img" aria-label="Blue digital circuit graphic with a hand" style="background:linear-gradient(135deg,#0e2a5a,#2f6cb8 60%,#9cc6ec)"></div><div class="body"><div class="date">24</div><div><h4>New rules for data at work.</h4><div class="meta">By admin - 3 news, business</div><p>What the latest data law means for firms, and the steps your team should take now.</p></div></div></article>
    <article class="post"><div class="pic" role="img" aria-label="Team joining puzzle pieces together" style="background:linear-gradient(135deg,#b9c6d6,#6f8aa8 50%,#c84a3a)"></div><div class="body"><div class="date">24</div><div><h4>How to plan a merger well.</h4><div class="meta">By admin - 3 news, business</div><p>Key checks to make before two firms join, from contracts to staff and tax.</p></div></div></article>
    <article class="post"><div class="pic" role="img" aria-label="Desk with calculator, papers and coffee" style="background:linear-gradient(135deg,#e8e2d6,#b9a78a 55%,#6d5a44)"></div><div class="body"><div class="date">24</div><div><h4>Smart tools for contracts.</h4><div class="meta">By admin - 3 news, business</div><p>Software can now draft and review deals fast. Here is how to use it safely.</p></div></div></article>
  </div>
  <div class="dots"><span class="on"></span><span></span><span></span><span></span></div>
</section>

<section class="callback">
  <h2>Request<br>A Call Back.</h2>
  <p class="cb-text">Leave your details and one of our lawyers will call you back within one working day to talk through your question at no cost... [+]</p>
  <div class="cb-form">
    <div class="lbl">Please fill up bellow form:</div>
    <div class="fields"><div class="field">Name</div><div class="field">Email</div><div class="field">Phone</div><div class="field">Message</div></div>
    <span class="submit">SUBMIT</span>
  </div>
</section>

<footer class="site-footer">
  <div class="foot-photo" role="img" aria-label="Dim city skyline at night"></div>
  <div class="foot-cols">
    <div><svg width="20" height="24" viewBox="0 0 20 24"><path d="M10 1a8 8 0 0 0-8 8c0 6 8 14 8 14s8-8 8-14a8 8 0 0 0-8-8z" fill="none" stroke="#fff" stroke-width="1.6"/><circle cx="10" cy="9" r="3" fill="#fff"/></svg>12 Lorem Street 456, Geneva</div>
    <div><svg width="22" height="22" viewBox="0 0 24 24"><path fill="none" stroke="#fff" stroke-width="1.6" d="M6.6 10.8a15 15 0 0 0 6.6 6.6l2.2-2.2c.3-.3.7-.4 1-.2 1.1.4 2.3.6 3.6.6.6 0 1 .4 1 1V20c0 .6-.4 1-1 1A17 17 0 0 1 3 4c0-.6.4-1 1-1h3.5c.6 0 1 .4 1 1 0 1.3.2 2.5.6 3.6.1.3 0 .7-.2 1z"/></svg>Phone: (00) 22 555 0142</div>
    <div><svg width="22" height="22" viewBox="0 0 24 24"><path d="M2 12L22 3l-6 19-4-8z" fill="none" stroke="#fff" stroke-width="1.6"/></svg>Email: info@kova.com</div>
  </div>
  <div class="foot-rule"></div>
  <div class="foot-brand">KOVA</div>
  <p class="foot-text">Smart legal services for modern business. Clear advice, fair fees and tools that save time for every client we serve.</p>
  <div class="hours"><span>MON - FRI: 8:00 - 17:00</span><span>SATURDAY: 9:00 - 15:00</span><span>SUNDAY: CLOSED</span></div>
  <span class="foot-btn">CONTACT US</span>
</footer>

<div class="copy">
  <span>Copyright © 2016 KOVA . All Right Reserved.</span>
  <div class="social"><span style="background:#3b5a9a"></span><span style="background:#2a7ab3"></span><span style="background:#3aa0d8"></span><span style="background:#cf4433"></span></div>
</div>

</body>
</html>
```